K & R Acre Works. Business card design

We need a business card designed for a new business. We have a bulldozer and tractor service. We clear land and make wildlife food plots. We provide disking, bush hogging, and site prep services.
I have attached an image of a business card that I like and would like my business cards to look similar.

Target Market(s)

anyone needing bulldozer and/or tractor services

Industry/Entity Type

Business

Contact Information for Business Card

K & R Acre Works, Operated by 7-T-Ranch
Wade Colton
601-472-3358
wcr4817@fieldmail-example.com

Font styles to use
Sans Serif

Colors

Designer to choose colors to be used in the design.

Requirements
Must have
• image of tractor and bulldozer
• Land Clearing
• Wildlife food plots
• Bush Hogging
• Disking
• Site prep
Nice to have
• i have included a image of a business card that i like. I would like mine to be similar.

```html
<!DOCTYPE html>
<html lang="en">
<head>
<meta charset="utf-8">
<title>K &amp; R Acre Works – Business Card</title>
<link rel="stylesheet" href="https://fonts.googleapis.com/css2?family=Oswald:wght@400;500;600&family=Raleway:wght@300&family=Roboto:wght@300&display=swap">
<style>
  :root {
    --page-bg: #e9e7e3;
    --card-white: #ffffff;
    --accent-red: #e2453f;
    --ink-dark: #2b2b2b;
    --ink-soft: #3d3d3d;
    --grass-deep: #2f5a22;
    --grass-mid: #5d8f3a;
    --grass-light: #8fba5a;
    --machine-yellow: #d9b53a;
    --earth-brown: #5b4a37;
  }
  * { margin: 0; padding: 0; box-sizing: border-box; }
  html, body {
    width: 1200px; height: 1023px; overflow: hidden;
    background: var(--page-bg);
  }
  .canvas {
    width: 1200px; height: 1023px;
    display: flex; align-items: center; justify-content: center;
  }
  .business-card {
    position: relative;
    width: 1000px; height: 571px;
    border-radius: 28px;
    overflow: hidden;
    background: var(--card-white);
    box-shadow: 0 10px 30px rgba(0,0,0,0.18);
  }
  .equipment-photo {
    position: absolute; inset: 0 0 auto 0; height: 340px;
    background:
      radial-gradient(ellipse 340px 180px at 640px 200px, var(--earth-brown) 0%, rgba(91,74,55,0.6) 45%, transparent 75%),
      radial-gradient(ellipse 220px 110px at 430px 270px, var(--machine-yellow) 0%, rgba(217,181,58,0.4) 50%, transparent 80%),
      linear-gradient(160deg, var(--grass-light) 0%, var(--grass-mid) 40%, var(--grass-deep) 100%);
  }
  .swoop { position: absolute; inset: 0; width: 1000px; height: 571px; }
  .brand {
    position: absolute; left: 62px; top: 72px;
    color: var(--card-white);
  }
  .brand-name {
    font-family: "Oswald", sans-serif; font-weight: 600;
    font-size: 68px; line-height: 1; letter-spacing: 0.5px;
    text-transform: uppercase;
    text-shadow: 0 2px 6px rgba(0,0,0,0.35);
  }
  .brand-operator {
    font-family: "Raleway", sans-serif; font-weight: 300;
    font-size: 27px; letter-spacing: 9px; margin-top: 8px;
    text-transform: uppercase;
    text-shadow: 0 1px 4px rgba(0,0,0,0.4);
  }
  .contact {
    position: absolute; left: 62px; top: 330px;
  }
  .owner-name {
    font-family: "Oswald", sans-serif; font-weight: 500;
    font-size: 46px; line-height: 1; color: var(--accent-red);
    text-transform: uppercase; letter-spacing: 0.5px;
  }
  .contact-line {
    display: flex; align-items: center; gap: 16px;
    font-family: "Roboto", sans-serif; font-weight: 300;
    font-size: 28px; line-height: 1.2; color: var(--ink-soft); margin-top: 8px;
  }
  .contact-line svg { width: 22px; height: 22px; flex: none; }
  .services {
    margin-top: 14px;
    font-family: "Oswald", sans-serif; font-weight: 400;
    font-size: 21px; line-height: 1.3; color: var(--ink-dark);
    text-transform: uppercase;
  }
  .services .sep { color: var(--accent-red); padding: 0 6px; }
</style>
</head>
<body>
<main class="canvas">
  <section class="business-card">
    <div class="equipment-photo" role="img" aria-label="Photo of a yellow bulldozer and tractor working in a green overgrown field"></div>

    <svg class="swoop" viewBox="0 0 1000 571" aria-hidden="true">
      <path d="M0 260 Q 330 390 1000 200 L1000 571 L0 571 Z" fill="var(--card-white)"/>
      <path d="M0 250 Q 330 380 1000 190" fill="none" stroke="var(--accent-red)" stroke-width="9"/>
    </svg>

    <header class="brand">
      <h1 class="brand-name">K &amp; R Acre Works</h1>
      <p class="brand-operator">Operated by 7-T-Ranch</p>
    </header>

    <div class="contact">
      <h2 class="owner-name">Wade Colton</h2>
      <p class="contact-line">
        <svg viewBox="0 0 24 24"><path d="M6.6 3.5c.4-.4 1-.4 1.4 0l2.3 2.6c.3.4.3.9 0 1.3L8.9 9c1.2 2.5 3.4 4.7 5.9 5.9l1.6-1.4c.4-.3.9-.3 1.3 0l2.6 2.3c.4.4.4 1 0 1.4l-1.6 1.8c-.6.6-1.5.8-2.3.5C10.6 17.6 6.4 13.4 4.5 7.6c-.3-.8-.1-1.7.5-2.3z" fill="var(--accent-red)"/></svg>
        601-472-3358
      </p>
      <p class="contact-line">
        <svg viewBox="0 0 24 24"><rect x="3" y="5" width="18" height="14" fill="none" stroke="var(--accent-red)" stroke-width="2"/><path d="M3 5l9 8 9-8" fill="none" stroke="var(--accent-red)" stroke-width="2"/></svg>
        wcr4817@fieldmail-example.com
      </p>
      <p class="services">
        Land Clearing<span class="sep">-</span>Wildlife Food Plots<br>
        Bush Hogging<span class="sep">-</span>Disking<span class="sep">-</span>Site Prep
      </p>
    </div>
  </section>
</main>
</body>
</html>
```